Marwick Law Letterhead

We need a new letterhead design for a Law Firm. The address for the law firm is 1475 Calloway Street, Suite 210, Houston, Texas 77041. Phone Number: 832-361-9027; Fax Number: 832-614-7359. The logo is uploaded to the project.

```html
<!DOCTYPE html>
<html lang="en">
<head>
<meta charset="utf-8">
<title>Marwick Law Letterhead</title>
<link rel="stylesheet" href="https://fonts.googleapis.com/css2?family=Montserrat:wght@400;500;600&display=swap">
<style>
  :root {
    --backdrop: #e8e8ea;
    --paper: #ffffff;
    --ink: #1c1c1c;
    --navy: #1b3160;
    --red: #d71920;
    --red-deep: #7a0b12;
  }
  * { box-sizing: border-box; margin: 0; padding: 0; }
  html, body { width: 1200px; height: 960px; overflow: hidden; }
  body {
    background: var(--backdrop);
    font-family: "Montserrat", Arial, sans-serif;
    color: var(--ink);
    position: relative;
  }
  .letterhead {
    position: absolute;
    left: 282px; top: 30px;
    width: 636px; height: 900px;
    background: var(--paper);
    box-shadow: 0 4px 18px rgba(0,0,0,0.12);
    overflow: hidden;
  }
  .wave { position: absolute; left: 0; top: 0; width: 636px; height: 900px; }
  .brand {
    position: absolute; left: 48px; top: 52px;
    display: flex; align-items: center; gap: 10px;
  }
  .brand-dot {
    width: 30px; height: 30px; border-radius: 50%;
    background: var(--navy);
  }
  .brand-name {
    font-size: 24px; font-weight: 600; color: var(--navy);
    letter-spacing: 0.5px;
  }
  .contact {
    position: absolute; left: 420px; top: 46px;
    padding-left: 14px;
    border-left: 1px solid var(--red);
    font-size: 9.5px; line-height: 1.45;
    font-style: normal;
  }
  .contact-phone { display: flex; align-items: center; gap: 6px; }
  .contact-phone svg { width: 9px; height: 9px; fill: var(--red); }
  .recipient {
    position: absolute; left: 70px; top: 190px;
    font-size: 11px; line-height: 1.45;
  }
  .body-copy {
    position: absolute; left: 104px; top: 262px; width: 470px;
    font-size: 10.2px; line-height: 1.5;
  }
  .body-copy p { margin-bottom: 16px; }
  .closing {
    position: absolute; left: 104px; top: 742px;
    font-size: 11.5px;
  }
  .signature {
    margin-top: 8px; width: 90px; height: 30px;
    background: linear-gradient(90deg, #d9d9d9, #eeeeee);
    border-radius: 3px;
  }
</style>
</head>
<body>
  <main class="letterhead">
    <svg class="wave" viewBox="0 0 636 900" aria-hidden="true">
      <defs>
        <linearGradient id="redSweep" x1="0" y1="1" x2="1" y2="0">
          <stop offset="0" stop-color="#d71920"/>
          <stop offset="0.6" stop-color="#c8151c"/>
          <stop offset="1" stop-color="#7a0b12"/>
        </linearGradient>
      </defs>
      <path fill="var(--navy)" d="M250 900 C290 850 330 840 400 836 C480 832 560 820 636 762 L636 900 Z"/>
      <path fill="var(--paper)" d="M266 900 C306 860 344 852 410 848 C490 844 570 834 636 784 L636 900 Z"/>
      <path fill="url(#redSweep)" d="M278 900 C318 868 354 862 420 858 C498 854 576 846 636 800 L636 900 Z"/>
    </svg>

    <header>
      <div class="brand">
        <span class="brand-dot"></span>
        <span class="brand-name">Marwick Law</span>
      </div>
      <address class="contact">
        <div>1475 Calloway Street,</div>
        <div>Suite 210, Houston,</div>
        <div>Texas 77041</div>
        <div class="contact-phone">
          <svg viewBox="0 0 24 24"><path d="M6.6 10.8a15.1 15.1 0 0 0 6.6 6.6l2.2-2.2a1 1 0 0 1 1-.25 11.4 11.4 0 0 0 3.6.57 1 1 0 0 1 1 1V20a1 1 0 0 1-1 1A17 17 0 0 1 3 4a1 1 0 0 1 1-1h3.5a1 1 0 0 1 1 1c0 1.25.2 2.45.57 3.57a1 1 0 0 1-.25 1z"/></svg>
          832-361-9027
        </div>
        <div class="contact-phone">
          <svg viewBox="0 0 24 24"><path d="M6 3h12v5H6zM4 9h16a2 2 0 0 1 2 2v6h-4v4H6v-4H2v-6a2 2 0 0 1 2-2zm4 7v3h8v-3z"/></svg>
          832-614-7359
        </div>
      </address>
    </header>

    <section class="recipient">
      <div>Mr/s</div>
      <div>First Name and Last Name</div>
      <div>Company Name</div>
      <div>Address</div>
    </section>

    <section class="body-copy">
      <p>Lorem ipsum dolor sit amet, consectetur adipiscing sed do eiusmod tempor incididunt laboreet dolore magna aliqua. Ut enim ad minim veniam, quis nostrud exercitation ullamco laboris nisi ut aliquip exea commodo consequat. Lorem ipsum dolor sit amet, consectetur adipiscing sed do eiusmod tempor incididunt labore et dolore magna aliqua. Ut enim</p>
      <p>Lorem ipsum dolor sit amet, consectetur adipiscing sed do eiusmod tempor incididunt labore et dolore magna aliqua. Ut enim ad minim veniam, quis nostrud exercitation ullamco laboris nisi ut aliquip exea commodo consequat. Duis aute irure dolor in reprehenderit in voluptate velit esse cillum irure dolor in reprehenderit in voluptate velit esse irure</p>
      <p>Lorem ipsum dolor sit amet, consectetur adipiscing sed do eiusmod tempor incididunt labore et dolore magna aliqua. consequat. Duis aute irure dolor in reprehenderit in voluptate velit esse cillum dolore eu fugiat nulla pariatur. Excepteur sint occaecat cupidatat non proident, sunt in culpa qui officia deserunt mollit,</p>
      <p>Lorem ipsum dolor sit amet, consectetur adipiscing sed do eiusmod tempor incididunt labore et dolore magna aliqua. Ut enim Lorem ipsum dolor sit amet, consectetur adipiscing sed do eiusmod tempor incididunt labore et dolore magna aliqua. Ut enim Lorem ipsum aliqua.ipsum</p>
      <p>Lorem ipsum dolor sit amet, consectetur adipiscing sed do eiusmod tempor incididunt labore et dolore magna aliqua. Ut enim ad minim veniam, quis nostrud exercitation ullamco laboris nisi ut aliquip exea commodo consequat. Duis aute irure dolor in reprehenderit in voluptate velit esse cillum irure dolor in reprehenderit in voluptate velit esse irure</p>
      <p>Lorem ipsum dolor sit amet, consectetur adipiscing sed do eiusmod tempor incididunt labore et dolore magna aliqua. Ut enim ad minim veniam, quis nostrud exercitation ullamco laboris nisi ut aliquip exea commodo consequat. Duis aute irure dolor in reprehenderit in voluptate velit esse cillum irure dolor in reprehenderit in voluptate velit esse irure</p>
    </section>

    <footer class="closing">
      <div>Regards</div>
      <div class="signature" role="img" aria-label="Handwritten signature of the sender"></div>
    </footer>
  </main>
</body>
</html>
```